ORIM Holding

ORIM holding is located in the UAE. In the company, there are several departments covering Hospitality management, Facility Management, interior design and Construction.

The logo should not include the name holding, Just ORIM.

Needed Items:

(1) Logo.
(2) Business Card.
(3) Letterhead
(4) Envelope
(5) cd cover
(6) email signature
Updates

The previous brief was misplaced with another competition. Current update is the final.

Target Market(s)

Collaboration with international high end firms.

Industry/Entity Type

Business

Requirements
Must have
• COLOR PREFERENCE Maximum 2 colors, preferably mono-color with different shades.
Nice to have
• Elegant, luxurious, and minimalistic.

```html
<!DOCTYPE html>
<html lang="en">
<head>
<meta charset="utf-8">
<title>ORIM Holding – Business Card</title>
<link href="https://fonts.googleapis.com/css2?family=Marcellus&family=Lato:wght@400&display=swap" rel="stylesheet">
<style>
  :root {
    --stage: #2b2b2b;
    --maroon: #4a0002;
    --crimson: #a3000f;
    --paper: #ffffff;
    --ink-light: #ffffff;
  }
  * { margin: 0; padding: 0; box-sizing: border-box; }
  html, body {
    width: 1200px; height: 1015px; overflow: hidden;
    background: var(--stage);
  }
  .canvas {
    position: relative; width: 1200px; height: 1015px;
  }
  .card {
    position: absolute; left: 250px; width: 700px; height: 400px;
    overflow: hidden; box-shadow: 0 10px 30px rgba(0,0,0,.55);
  }
  .card--front { top: 70px; background: var(--maroon); }
  .card--back { top: 535px; background: var(--maroon); }

  .brand {
    position: absolute; display: flex; flex-direction: column; align-items: center;
    font-family: "Marcellus", serif; letter-spacing: 4px;
  }
  .brand__mark {
    width: 92px; height: 92px; border-radius: 50%;
    border: 3px solid currentColor; margin-bottom: 26px;
  }
  .brand__name { font-size: 40px; white-space: nowrap; }
  .card--front .brand { left: 0; right: 0; top: 110px; color: var(--ink-light); }

  .back__art { position: absolute; inset: 0; }
  .card--back .brand { left: 400px; width: 300px; top: 70px; color: var(--crimson); }
  .card--back .brand__mark { width: 80px; height: 80px; border-color: var(--maroon); margin-bottom: 22px; }
  .card--back .brand__name { font-size: 30px; letter-spacing: 3px; }

  .holder {
    position: absolute; left: 46px; top: 120px; color: var(--ink-light);
  }
  .holder__name { font-family: "Marcellus", serif; font-size: 26px; letter-spacing: 2px; }
  .holder__role { font-family: "Lato", sans-serif; font-size: 16px; margin-top: 2px; }

  .contact {
    position: absolute; left: 46px; top: 232px; color: var(--ink-light);
    font-family: "Lato", sans-serif; font-size: 15px; line-height: 1.45;
  }
  .contact__address { margin-bottom: 14px; }
  .contact__row { display: flex; align-items: center; gap: 9px; }
  .contact__row svg { width: 15px; height: 15px; flex: none; }
</style>
</head>
<body>
<main class="canvas">

  <section class="card card--front" aria-label="Business card front">
    <div class="brand">
      <span class="brand__mark"></span>
      <span class="brand__name">ORIM HOLDING</span>
    </div>
  </section>

  <section class="card card--back" aria-label="Business card back">
    <svg class="back__art" viewBox="0 0 700 400" aria-hidden="true">
      <circle cx="590" cy="150" r="255" fill="none" stroke="var(--crimson)" stroke-width="3"/>
      <circle cx="600" cy="140" r="258" fill="var(--paper)"/>
    </svg>

    <div class="brand">
      <span class="brand__mark"></span>
      <span class="brand__name">ORIM HOLDING</span>
    </div>

    <div class="holder">
      <p class="holder__name">DANIEL HARPER</p>
      <p class="holder__role">Managing Director</p>
    </div>

    <div class="contact">
      <p class="contact__address">18, Marina Crest Avenue<br>Dubai, UAE, 20417</p>
      <p class="contact__row">
        <svg viewBox="0 0 16 16"><path fill="#fff" d="M3.6 1.5l2.3 2.6-1.3 1.7c.9 2 2.5 3.6 4.6 4.6l1.7-1.3 2.6 2.3-1.4 2.1C7 13.2 2.8 9 1.5 3z"/></svg>
        044-781 302 556
      </p>
      <p class="contact__row">
        <svg viewBox="0 0 16 16"><rect x="1" y="3" width="14" height="10" fill="none" stroke="#fff" stroke-width="1.5"/><path d="M1 3l7 6 7-6" fill="none" stroke="#fff" stroke-width="1.5"/></svg>
        hello@orimgroup.ae
      </p>
      <p class="contact__row">
        <svg viewBox="0 0 16 16"><circle cx="8" cy="8" r="6.5" fill="none" stroke="#fff" stroke-width="1.4"/><ellipse cx="8" cy="8" rx="3" ry="6.5" fill="none" stroke="#fff" stroke-width="1.2"/><path d="M1.5 8h13" stroke="#fff" stroke-width="1.2"/></svg>
        www.orimgroup-uae.com
      </p>
    </div>
  </section>

</main>
</body>
</html>
```